Oil Field Service company needs professional business cards

Looking to clean up our current company business cards and look a little more professional. Brenwick Casing Services is a US based company that services the oil field. We deal with engineers, managers and oil rigs....................................................................................................................................................................................................................................................................................................................................................................................................

Target Market(s)

Oil and Gas professionals

Industry/Entity Type

Oil And Gas

Contact Information for Business Card

See attached photo as example

Font styles to use
Sans Serif

Colors
ec1f27

Requirements
Must have
• Company Logo, Name, Title, Cell, Office, Fax, Email.
• See attached photo
Nice to have
• External CRT, Internal CRT, Casing Crews, Torque Turn, Laydown Machine
Should not have
• Do not introduce any new pictures and keep it professional looking

```html
<!DOCTYPE html>
<html lang="en">
<head>
<meta charset="utf-8">
<title>Brenwick Casing Services – Business Card</title>
<link href="https://fonts.googleapis.com/css2?family=Open+Sans:wght@400;600;700&display=swap" rel="stylesheet">
<style>
  :root {
    --stage: #2b2b2b;
    --card: #111112;
    --card-edge: #1c1c1e;
    --red: #ec1f27;
    --white: #f2f2f2;
    --muted: #cfcfcf;
  }
  * { margin: 0; padding: 0; box-sizing: border-box; }
  html, body {
    width: 1200px; height: 900px; overflow: hidden;
    background: var(--stage);
    font-family: "Open Sans", Arial, sans-serif;
  }
  .sheet {
    position: relative; width: 1200px; height: 900px;
    display: flex; flex-direction: column; align-items: center; justify-content: center; gap: 40px;
  }
  .card {
    position: relative; width: 700px; height: 400px;
    background: var(--card);
    border: 1px solid var(--card-edge);
    border-radius: 28px;
    overflow: hidden;
  }

  /* Company name block: plain set name with a single circle */
  .company { display: flex; align-items: center; gap: 12px; }
  .company-dot { width: 12px; height: 12px; border-radius: 50%; background: var(--red); flex: none; }
  .company-name { color: var(--white); font-weight: 600; font-size: 20px; line-height: 1.25; }

  /* Front */
  .card-front .company { position: absolute; left: 44px; top: 136px; width: 250px; }
  .divider {
    position: absolute; left: 318px; top: 60px; width: 1px; height: 190px;
    background: linear-gradient(to bottom, transparent, var(--red) 25%, var(--red) 75%, transparent);
    opacity: .7;
  }
  .contact { position: absolute; left: 346px; top: 64px; color: var(--white); }
  .contact-name { color: var(--red); font-weight: 700; font-size: 22px; line-height: 1.1; }
  .contact-title { font-size: 14px; color: var(--muted); margin-top: 2px; }
  .contact-list { list-style: none; margin-top: 28px; }
  .contact-list li { display: flex; align-items: center; gap: 12px; font-size: 16px; line-height: 24px; }
  .contact-list svg { width: 13px; height: 13px; fill: var(--red); flex: none; }
  .services {
    position: absolute; left: 44px; bottom: 56px;
    color: var(--red); font-weight: 600; font-size: 19px;
  }
  .services .sep { margin: 0 4px; }

  /* Back */
  .card-back { display: flex; align-items: center; justify-content: center; }
  .card-back .company-name { font-size: 26px; }
</style>
</head>
<body>
<main class="sheet">
  <section class="card card-front" aria-label="Business card front">
    <div class="company">
      <div class="company-dot"></div>
      <p class="company-name">Brenwick<br>Casing Services</p>
    </div>
    <div class="divider"></div>
    <div class="contact">
      <p class="contact-name">Cody Marlowe</p>
      <p class="contact-title">Area Manager</p>
      <ul class="contact-list">
        <li><svg viewBox="0 0 16 16" aria-hidden="true"><path d="M3.5 1.5l2.5 0 1.2 3.2-1.6 1.2c.8 1.8 2.2 3.2 4 4l1.2-1.6 3.2 1.2v2.5c0 .8-.7 1.5-1.5 1.5C6.4 13.5 2 9.1 2 3c0-.8.7-1.5 1.5-1.5z"/></svg>(555) 410-2200</li>
        <li><svg viewBox="0 0 16 16" aria-hidden="true"><path d="M5 1h6a1 1 0 0 1 1 1v12a1 1 0 0 1-1 1H5a1 1 0 0 1-1-1V2a1 1 0 0 1 1-1zm0 2v9h6V3H5zm3 10a.8.8 0 1 0 0 1.6.8.8 0 0 0 0-1.6z"/></svg>(555) 410-7381</li>
        <li><svg viewBox="0 0 16 16" aria-hidden="true"><path d="M4 1h6l2 2v3h1a2 2 0 0 1 2 2v5a2 2 0 0 1-2 2H3a2 2 0 0 1-2-2V8a2 2 0 0 1 2-2h1V1zm1 1v4h6V3.5L9.5 2H5zm-1 7v1h2V9H4zm4 0v1h2V9H8zm-4 2v1h2v-1H4zm4 0v1h2v-1H8z"/></svg>(555) 410-6614</li>
        <li><svg viewBox="0 0 16 16" aria-hidden="true"><path d="M2 3h12a1 1 0 0 1 1 1v8a1 1 0 0 1-1 1H2a1 1 0 0 1-1-1V4a1 1 0 0 1 1-1zm0 1.5V5l6 4 6-4v-.5H2z"/></svg>cody.marlowe@brenwickmail.com</li>
      </ul>
    </div>
    <p class="services">Laydown Machine<span class="sep">|</span>Casing Crew<span class="sep">|</span>Mud Tool<span class="sep">|</span>Torque Turn</p>
  </section>

  <section class="card card-back" aria-label="Business card back">
    <div class="company">
      <div class="company-dot"></div>
      <p class="company-name">Brenwick Casing Services</p>
    </div>
  </section>
</main>
</body>
</html>
```